KDWB Business Card

Looking for a business card design to incorporate our branding. We want to only use the colors listing in the Branding Package (attached).
Updates

Target Market(s)

People who need their phone or device fixed.

Industry/Entity Type

Electronics

Contact Information for Business Card

Please use:

Brightwick Gadget Clinic LLC
4810 E Harlow Ridge Rd
Suite 417
San Antonio, TX 78163

Marcus Delgrove, Store Manager

(210) 555-0147

Requirements
Must have
• Must include the colors that are contained within the Branding Package PDF file.

```html
<!DOCTYPE html>
<html lang="en">
<head>
<meta charset="utf-8">
<title>Brightwick Gadget Clinic – Business Card</title>
<link rel="stylesheet" href="https://fonts.googleapis.com/css2?family=Questrial&display=swap">
<style>
  :root {
    --orange: #f05a22;
    --orange-soft: #fdf3ee;
    --grey: #55575a;
    --ink: #3a3a3c;
    --paper: #ffffff;
    --backdrop: #e6e6e6;
  }
  html, body {
    margin: 0;
    padding: 0;
    width: 1200px;
    height: 873px;
    overflow: hidden;
    background: var(--backdrop);
    font-family: "Questrial", Arial, sans-serif;
  }
  .canvas {
    position: relative;
    width: 1200px;
    height: 873px;
    display: flex;
    align-items: center;
    justify-content: center;
    gap: 44px;
  }
  .card {
    position: relative;
    width: 520px;
    height: 297px;
    background: var(--paper);
    box-shadow: 0 6px 18px rgba(0,0,0,0.12);
    overflow: hidden;
  }
  /* brand lockup */
  .brand {
    position: absolute;
    display: flex;
    align-items: center;
    gap: 10px;
  }
  .brand-mark {
    width: 30px;
    height: 30px;
    background: var(--orange);
    border-radius: 7px;
    flex: none;
  }
  .brand-name {
    color: var(--orange);
    font-size: 22px;
    line-height: 1.1;
    letter-spacing: 0.2px;
  }
  /* front */
  .card-front .brand { top: 30px; right: 34px; }
  .faint-square {
    position: absolute;
    right: 46px;
    bottom: 52px;
    width: 170px;
    height: 150px;
    border-radius: 34px;
    background: var(--orange-soft);
  }
  .person {
    position: absolute;
    left: 36px;
    top: 96px;
  }
  .person-name {
    margin: 0;
    font-size: 19px;
    color: var(--ink);
    font-weight: 400;
  }
  .person-title {
    margin: 3px 0 0;
    font-size: 11px;
    color: var(--orange);
  }
  .contact {
    position: absolute;
    left: 36px;
    top: 164px;
    margin: 0;
    padding: 0;
    list-style: none;
    font-size: 13px;
    color: var(--ink);
  }
  .contact li {
    display: flex;
    align-items: center;
    gap: 9px;
    margin-bottom: 9px;
  }
  .contact-icon {
    width: 14px;
    height: 14px;
    background: var(--orange);
    border-radius: 2px;
    display: flex;
    align-items: center;
    justify-content: center;
    flex: none;
  }
  .band-grey {
    position: absolute;
    left: 0;
    bottom: 0;
    width: 100%;
    height: 20px;
    background: var(--grey);
  }
  .band-orange {
    position: absolute;
    left: 0;
    bottom: 26px;
    width: 210px;
    height: 9px;
    background: var(--orange);
  }
  /* back */
  .card-back .brand {
    top: 50%;
    left: 50%;
    transform: translate(-50%, -50%);
    gap: 14px;
  }
  .card-back .brand-mark { width: 40px; height: 40px; border-radius: 9px; }
  .card-back .brand-name { font-size: 30px; }
</style>
</head>
<body>
<main class="canvas">
  <section class="card card-front" aria-label="Business card front">
    <div class="faint-square"></div>
    <div class="brand">
      <span class="brand-mark"></span>
      <span class="brand-name">Brightwick Gadget Clinic</span>
    </div>
    <div class="person">
      <h1 class="person-name">Marcus Delgrove</h1>
      <p class="person-title">Store Manager</p>
    </div>
    <ul class="contact">
      <li>
        <span class="contact-icon">
          <svg width="9" height="9" viewBox="0 0 24 24" aria-hidden="true"><path fill="#fff" d="M6.6 10.8a15.1 15.1 0 0 0 6.6 6.6l2.2-2.2c.3-.3.7-.4 1-.2 1.1.4 2.3.6 3.6.6.6 0 1 .4 1 1V20c0 .6-.4 1-1 1A17 17 0 0 1 3 4c0-.6.4-1 1-1h3.5c.6 0 1 .4 1 1 0 1.3.2 2.5.6 3.6.1.3 0 .7-.2 1z"/></svg>
        </span>
        (210) 555-0147
      </li>
      <li>
        <span class="contact-icon">
          <svg width="9" height="9" viewBox="0 0 24 24" aria-hidden="true"><path fill="#fff" d="M12 2a7 7 0 0 0-7 7c0 5.2 7 13 7 13s7-7.8 7-13a7 7 0 0 0-7-7zm0 9.5A2.5 2.5 0 1 1 12 6.5a2.5 2.5 0 0 1 0 5z"/></svg>
        </span>
        4810 E Harlow Ridge Rd, Suite 417, San Antonio, TX 78163
      </li>
    </ul>
    <div class="band-orange"></div>
    <div class="band-grey"></div>
  </section>

  <section class="card card-back" aria-label="Business card back">
    <div class="brand">
      <span class="brand-mark"></span>
      <span class="brand-name">Brightwick Gadget Clinic</span>
    </div>
  </section>
</main>
</body>
</html>
```